A gateway to the eyes of potential Talquen Candidates and Clients

We are looking for a brochure that will grab attention, all most along the lines of an infogram. The business supplies people to the construction sector. So we want it simple but sharp.

I would like the brochure to be able to have a half fold effect when printed but the main focus will be to use it in an e-brochure format.

Main pages will be as follows:

About Us: Which will have a bit about the management team and some pictures.

Services: information for both candidate and clients.

Why us?:

Contact: Location, contact numbers etc.

FOR CONTENTS:
website will give you the content required. www.talquenbuilders.co.uk
Updates

Project Deadline Extended Reason: Project was moved from a flyer to a brochure and the logo didn't upload. So I will be uploading my new logo and it will give additional time to get designs in. Cheers Added Monday, June 20, 2016

Target Market(s)

Clients and candidates for the construction market

Industry/Entity Type

Business

Requirements
Must have
• Bold and strong images of the construction sector. A simple to read format. Also needs to look good in an electronic format.
Nice to have
• I like the idea of a black and white model but with certain parts of the images highlighted in our colours.
Should not have
• Too much of a complex lay out.

```html
<!DOCTYPE html>
<html lang="en">
<head>
<meta charset="utf-8">
<title>Talquen Construction – Brochure Cover</title>
<link href="https://fonts.googleapis.com/css2?family=Jost:wght@400;500&family=Open+Sans:wght@400;600;700&display=swap" rel="stylesheet">
<style>
  :root {
    --backdrop: #8f8f8f;
    --paper: #ffffff;
    --ink: #3a3a3a;
    --orange: #f0a21a;
    --orange-deep: #e57d17;
    --blue: #1a8fd6;
    --blue-deep: #0d6db4;
    --photo-light: #dfe6ec;
    --photo-mid: #b9c5cf;
  }
  * { box-sizing: border-box; margin: 0; padding: 0; }
  html, body { width: 1200px; height: 804px; overflow: hidden; }
  body {
    background: var(--backdrop);
    display: flex;
    align-items: center;
    justify-content: center;
    font-family: "Open Sans", Arial, sans-serif;
  }
  .cover {
    position: relative;
    width: 540px;
    height: 764px;
    background: var(--paper);
    box-shadow: 0 6px 22px rgba(0,0,0,0.25);
    overflow: hidden;
  }
  .tagline {
    position: absolute;
    left: 34px;
    top: 62px;
    font-size: 14px;
    color: var(--ink);
  }
  .brand {
    position: absolute;
    right: 36px;
    top: 34px;
    display: flex;
    align-items: center;
    gap: 7px;
    font-family: "Open Sans", Arial, sans-serif;
    font-weight: 700;
    font-size: 18px;
    letter-spacing: 1px;
    color: var(--orange-deep);
  }
  .brand-mark {
    width: 14px;
    height: 14px;
    background: var(--blue);
  }
  .hero-photo {
    position: absolute;
    left: 0;
    top: 92px;
    width: 540px;
    height: 350px;
    background: linear-gradient(180deg, var(--photo-light) 0%, var(--photo-mid) 100%);
  }
  .band {
    position: absolute;
    top: 442px;
    height: 180px;
  }
  .band-quote {
    left: 0;
    width: 210px;
    background: linear-gradient(160deg, var(--orange) 0%, var(--orange-deep) 100%);
  }
  .band-title {
    left: 210px;
    width: 330px;
    background: linear-gradient(160deg, var(--blue) 0%, var(--blue-deep) 100%);
    color: #fff;
    padding: 52px 28px 0 34px;
  }
  .quote-icon {
    position: absolute;
    left: 34px;
    top: 96px;
    width: 26px;
    height: 26px;
  }
  .quote {
    position: absolute;
    left: 68px;
    top: 84px;
    width: 130px;
    font-size: 10.5px;
    font-weight: 600;
    line-height: 1.15;
    color: #fff;
    letter-spacing: 0.5px;
  }
  .quote cite {
    font-style: normal;
    font-weight: 400;
    font-size: 6px;
    color: #5a3a05;
    margin-left: 4px;
  }
  .title {
    font-family: "Jost", "Futura", sans-serif;
    font-weight: 400;
    font-size: 25px;
    letter-spacing: 0.5px;
  }
  .intro {
    margin-top: 24px;
    font-size: 8.5px;
    line-height: 1.5;
  }
  .web {
    position: absolute;
    left: 0;
    right: 0;
    top: 696px;
    text-align: center;
    font-size: 10px;
    letter-spacing: 2px;
    color: var(--ink);
  }
</style>
</head>
<body>
  <article class="cover">
    <p class="tagline">Be a better version of you...</p>
    <div class="brand"><span class="brand-mark"></span>TALQUEN</div>

    <div class="hero-photo" role="img" aria-label="Construction team in hard hats and hi-vis vests meeting around a table, city skyline and cranes through tall windows"></div>

    <section class="band band-quote">
      <svg class="quote-icon" viewBox="0 0 26 26" aria-hidden="true">
        <rect x="0" y="0" width="16" height="16" fill="#2b2b2b"/>
        <rect x="8" y="8" width="18" height="18" fill="#ffffff"/>
      </svg>
      <p class="quote">“Your life does not get better by chance, it gets better by change” <cite>DALE MARLOW</cite></p>
    </section>

    <section class="band band-title">
      <h1 class="title">TALQUEN Construction</h1>
      <p class="intro">Fresh start? New Job? Brighter Future? A Better you? Talquen Construction is in your corner.</p>
    </section>

    <p class="web">www.talquenbuilders.co.uk</p>
  </article>
</body>
</html>
```